Zolvana Stationary and Branding Documents

Corporate Identity Branding stationary needed for IT Recruiting Firm.

I already have a Logo, business cards and website. I need to get designs completed for the remaining corporate identity documents.

The documentation should use similar colors as my website and business card. The designs should modern and clean.

http://zolvanaworks.example/

Target Market(s)

Information Technology Industry

Industry/Entity Type

Information Technology

Colors
3377b5
0255a3
fbee3e
f78f20
f37122
33a6d7
000000
0592cd

Requirements
Must have
• Letter Head
• Folder Design
• PowerPoint Design
• Invoice
• Envelope
Nice to have
• Proposal
• Flyer
• Brochure
Should not have
• Logo
• Business Cards
• Website

```html
<!DOCTYPE html>
<html lang="en">
<head>
<meta charset="utf-8">
<title>Zolvana – PowerPoint Presentation</title>
<link rel="stylesheet" href="https://fonts.googleapis.com/css2?family=Jost:wght@400;500;600&family=Open+Sans:wght@400&display=swap">
<style>
  :root {
    --blue: #0255a3;
    --venn: #1f57a8;
    --dark: #2e2e2e;
    --rule: #333333;
    --bg-light: #d2d3d5;
    --bg-dark: #c6c7c9;
    --paper: #ffffff;
    --body: #333333;
    --muted: #6b6b6b;
  }
  * { box-sizing: border-box; margin: 0; padding: 0; }
  html, body { width: 1200px; height: 1200px; overflow: hidden; }
  body { position: relative; font-family: "Jost", sans-serif; background: var(--bg-light); }
  .backdrop { position: absolute; inset: 0; }
  .heading {
    position: absolute; left: 144px; top: 160px; width: 952px; height: 92px;
    border: 2px dashed var(--rule);
    display: flex; align-items: center; justify-content: center;
  }
  .heading h1 { font-weight: 600; font-size: 58px; color: var(--blue); letter-spacing: -0.5px; line-height: 1; white-space: nowrap; }
  .slide {
    position: absolute; width: 356px; height: 274px; background: var(--paper);
    overflow: hidden; box-shadow: 6px 8px 14px rgba(0,0,0,0.12);
  }
  .slide .band { position: absolute; left: 0; bottom: 0; width: 356px; height: 274px; }
  .abs { position: absolute; }
  .title { color: var(--blue); font-weight: 600; font-size: 22px; line-height: 1; white-space: nowrap; }
  .title-rule { position: absolute; height: 1.5px; background: var(--rule); }
  .copy { font-family: "Open Sans", sans-serif; font-size: 6.5px; line-height: 1.3; color: var(--body); }
  .copy.tiny { font-size: 4.6px; color: var(--muted); }
  .brand { font-size: 44px; font-weight: 500; color: var(--blue); line-height: 1; }
  .team { background: linear-gradient(180deg, #4a4f57, #33373d); }
  .tag { position: absolute; width: 131px; height: 21px; color: #fff; font-size: 12px; font-weight: 500; padding-left: 5px; line-height: 21px; white-space: nowrap; }
  .tag.blue { background: var(--blue); }
  .tag.dark { background: var(--dark); }
  .step-num { font-size: 21px; font-weight: 500; color: var(--blue); line-height: 1; }
  .keyword { font-size: 10.5px; font-weight: 500; color: var(--dark); line-height: 1; }
</style>
</head>
<body>
<svg class="backdrop" width="1200" height="1200" aria-hidden="true">
  <rect width="1200" height="1200" fill="var(--bg-light)"/>
  <polygon points="1200,0 1200,1200 0,1200 0,1100" fill="var(--bg-dark)"/>
</svg>

<header class="heading"><h1>POWERPOINT PRESENTATION</h1></header>

<!-- Cover -->
<section class="slide" style="left:52px;top:374px">
  <div class="abs brand" style="left:100px;top:68px">Zolvana</div>
  <div class="abs team" role="img" aria-label="Illustration of a group of business people" style="left:110px;top:154px;width:140px;height:80px"></div>
  <svg class="band" viewBox="0 0 356 274" aria-hidden="true"><polygon points="0,218 230,242 0,270" fill="var(--dark)"/><polygon points="0,267 356,211 356,274 0,274" fill="var(--blue)"/></svg>
</section>

<!-- Agenda -->
<section class="slide" style="left:425px;top:374px">
  <div class="tag blue" style="left:34px;top:52px">1. TITLE GOES HERE</div>
  <div class="tag dark" style="left:34px;top:90px">2. TITLE GOES HERE</div>
  <div class="tag blue" style="left:34px;top:129px">3. TITLE GOES HERE</div>
  <div class="tag dark" style="left:195px;top:52px">4. TITLE GOES HERE</div>
  <div class="tag blue" style="left:195px;top:90px">5. TITLE GOES HERE</div>
  <div class="tag dark" style="left:195px;top:129px">6. TITLE GOES HERE</div>
  <p class="abs copy" style="left:32px;top:162px;width:138px">Lorem ipsum dolor sit amet, consectetur adipiscing elit. Morbi interdum eget felis non tempor. Morbi faucibus, libero a posuere.</p>
  <p class="abs copy" style="left:194px;top:162px;width:138px">Lorem ipsum dolor sit amet, consectetur adipiscing elit. Morbi interdum eget felis non tempor. Morbi faucibus, libero a posuere.</p>
  <svg class="band" viewBox="0 0 356 274" aria-hidden="true"><polygon points="0,218 230,242 0,270" fill="var(--dark)"/><polygon points="0,267 356,211 356,274 0,274" fill="var(--blue)"/></svg>
</section>

<!-- Venn -->
<section class="slide" style="left:800px;top:374px">
  <div class="abs title" style="left:30px;top:57px">TITLE GOES HERE</div>
  <div class="title-rule" style="left:30px;top:82px;width:301px"></div>
  <p class="abs copy tiny" style="left:30px;top:112px;width:95px">Lorem ipsum dolor sit amet, consectetur adipiscing elit.</p>
  <p class="abs copy tiny" style="left:30px;top:156px;width:95px">Lorem ipsum dolor sit amet, consectetur adipiscing elit. Morbi interdum eget felis non tempor. Morbi faucibus, libero a posuere.</p>
  <p class="abs copy tiny" style="left:240px;top:112px;width:95px">Lorem ipsum dolor sit amet, consectetur adipiscing elit. Morbi interdum eget felis non tempor. Morbi faucibus, libero a posuere.</p>
  <p class="abs copy tiny" style="left:240px;top:156px;width:95px">Lorem ipsum dolor sit amet, consectetur adipiscing elit. Morbi interdum eget felis non tempor. Morbi faucibus, libero a posuere.</p>
  <svg class="abs" style="left:0;top:0" width="356" height="274" aria-hidden="true">
    <g fill="var(--venn)" fill-opacity="0.8">
      <circle cx="179" cy="131" r="30"/><circle cx="158" cy="167" r="30"/><circle cx="200" cy="167" r="30"/>
    </g>
    <g fill="#fff" font-family="Jost, sans-serif" font-size="20" text-anchor="middle">
      <text x="179" y="133">A</text><text x="157" y="175">B</text><text x="201" y="175">C</text>
    </g>
  </svg>
  <svg class="band" viewBox="0 0 356 274" aria-hidden="true"><polygon points="0,218 230,242 0,270" fill="var(--dark)"/><polygon points="0,267 356,211 356,274 0,274" fill="var(--blue)"/></svg>
</section>

<!-- Steps -->
<section class="slide" style="left:52px;top:694px">
  <div class="abs title" style="left:27px;top:54px">TITLE GOES HERE</div>
  <div class="title-rule" style="left:27px;top:79px;width:299px"></div>
  <svg class="abs" style="left:0;top:0" width="356" height="274" aria-hidden="true">
    <g fill="var(--blue)">
      <rect x="27" y="131" width="44" height="12"/>
      <polygon points="66,120 100,120 100,113 118,127 100,141 100,134 66,134"/>
      <rect x="131" y="131" width="44" height="12"/>
      <polygon points="170,120 204,120 204,113 222,127 204,141 204,134 170,134"/>
      <rect x="235" y="131" width="44" height="12"/>
      <polygon points="274,120 308,120 308,113 326,127 308,141 308,134 274,134"/>
    </g>
  </svg>
  <div class="abs step-num" style="left:27px;top:106px">01</div>
  <div class="abs step-num" style="left:131px;top:106px">02</div>
  <div class="abs step-num" style="left:235px;top:106px">03</div>
  <div class="abs keyword" style="left:65px;top:98px">KEYWORD</div>
  <div class="abs keyword" style="left:169px;top:98px">KEYWORD</div>
  <div class="abs keyword" style="left:273px;top:98px">KEYWORD</div>
  <p class="abs copy tiny" style="left:27px;top:160px;width:96px">Lorem ipsum dolor sit amet, consectetur adipiscing elit. Morbi interdum eget felis non tempor.</p>
  <p class="abs copy tiny" style="left:131px;top:160px;width:96px">Lorem ipsum dolor sit amet, consectetur adipiscing elit. Morbi interdum eget felis non tempor.</p>
  <p class="abs copy tiny" style="left:235px;top:160px;width:96px">Lorem ipsum dolor sit amet, consectetur adipiscing elit. Morbi interdum eget felis non tempor.</p>
  <svg class="band" viewBox="0 0 356 274" aria-hidden="true"><polygon points="0,218 230,242 0,270" fill="var(--dark)"/><polygon points="0,267 356,211 356,274 0,274" fill="var(--blue)"/></svg>
</section>

<!-- Media + text -->
<section class="slide" style="left:425px;top:694px">
  <div class="abs title" style="left:35px;top:54px">TITLE GOES HERE</div>
  <svg class="abs" style="left:0;top:0" width="356" height="274" aria-hidden="true">
    <rect x="38" y="84" width="153" height="106" fill="none" stroke="var(--rule)" stroke-width="1" stroke-dasharray="2 2"/>
    <g opacity="0.7">
      <rect x="96" y="118" width="11" height="11" fill="#9fb7d6"/>
      <rect x="110" y="116" width="11" height="13" fill="#e3a64e"/>
      <rect x="124" y="118" width="11" height="11" fill="#8cc38b"/>
      <rect x="96" y="133" width="11" height="11" fill="#b7c9e0"/>
      <rect x="110" y="133" width="11" height="11" fill="#c9a6d3"/>
      <circle cx="129.5" cy="138.5" r="5.5" fill="#a9bfd9"/>
    </g>
  </svg>
  <p class="abs copy tiny" style="left:211px;top:83px;width:112px">Lorem ipsum dolor sit amet, consectetur adipiscing elit. Morbi interdum eget felis non tempor. Morbi faucibus, libero a posuere euismod, diam arcu tristique neque, sit amet tristique lorem justo sed magna. Nullam ligula elit, faucibus eu purus quis, sodales venenatis ex. Vestibulum suscipit, nisl sit.</p>
  <p class="abs copy tiny" style="left:211px;top:126px;width:112px">Aenean non elementum sem. Etiam bibendum commodo ex nec auctor. Aenean efficitur enim sed hendrerit porttitor. Morbi in justo iaculis, laoreet lectus eget, porta sapien. Aliquam purus urna, mattis vitae dignissim ac, ullamcorper nec nulla. Suspendisse eu aliquet nunc.</p>
  <p class="abs copy tiny" style="left:211px;top:168px;width:112px">Aenean non elementum sem. Etiam bibendum commodo ex nec auctor. Aenean efficitur enim sed hendrerit porttitor. Morbi in justo iaculis, laoreet lectus eget, porta sapien.</p>
  <svg class="band" viewBox="0 0 356 274" aria-hidden="true"><polygon points="0,218 230,242 0,270" fill="var(--dark)"/><polygon points="0,267 356,211 356,274 0,274" fill="var(--blue)"/></svg>
</section>

<!-- Chart -->
<section class="slide" style="left:800px;top:694px">
  <div class="abs title" style="left:30px;top:70px;font-size:17px">TITLE GOES HERE</div>
  <p class="abs copy tiny" style="left:30px;top:97px;width:140px">Lorem ipsum dolor sit amet, consectetur adipiscing elit. Morbi interdum eget felis non tempor. Morbi faucibus, libero a posuere euismod, diam arcu tristique neque, sit amet tristique lorem justo sed magna.</p>
  <p class="abs copy tiny" style="left:30px;top:128px;width:140px">Nullam ligula elit, faucibus eu purus quis, sodales venenatis ex. Vestibulum suscipit, nisl. Etiam bibendum commodo ex nec auctor.</p>
  <p class="abs copy tiny" style="left:30px;top:153px;width:140px">Nullam ligula elit, faucibus eu purus quis, sodales venenatis ex. Vestibulum suscipit, nisl. Etiam bibendum commodo ex nec auctor.</p>
  <svg class="abs" style="left:0;top:0" width="356" height="274" aria-hidden="true">
    <polyline points="216,62 216,164 330,164" fill="none" stroke="var(--blue)" stroke-width="1"/>
    <g fill="var(--blue)" font-family="Jost, sans-serif" font-size="9" text-anchor="middle">
      <text x="206" y="157">0</text><text x="206" y="139">1</text><text x="206" y="121">2</text>
      <text x="206" y="104">3</text><text x="206" y="86">4</text><text x="206" y="68">5</text>
      <text x="235" y="178">A</text><text x="256" y="178">B</text><text x="277" y="178">C</text>
      <text x="297" y="178">D</text><text x="318" y="178">E</text>
    </g>
    <rect x="228" y="117" width="14" height="37" fill="var(--dark)"/>
    <rect x="249" y="62" width="14" height="92" fill="var(--blue)"/>
    <rect x="270" y="82" width="14" height="72" fill="var(--blue)"/>
    <rect x="290" y="102" width="14" height="52" fill="var(--dark)"/>
    <rect x="311" y="82" width="14" height="72" fill="var(--blue)"/>
  </svg>
  <svg class="band" viewBox="0 0 356 274" aria-hidden="true"><polygon points="0,218 230,242 0,270" fill="var(--dark)"/><polygon points="0,267 356,211 356,274 0,274" fill="var(--blue)"/></svg>
</section>
</body>
</html>
```